Bold & Modern "Save the Date" Design for Medical Yacht Brunch Event

We are looking for a bold, modern, and eye-catching "Save the Date" design for a physician brunch event.
Event Overview:
This is a 2-hour brunch aboard a luxury yacht, hosted for a select group of physician investigators participating in our new LUMINA study. The event will take place during the upcoming GKTR medical conference.
Event Name:
LUMINA Study Network Forum
Date:
Saturday, July 19th (9:30am - 11:30am)
Location:
Marlo Belle yacht (docked directly outside of the Westerhaven)
Blurb:
Join us aboard Marlo Belle for a LUMINA Study Investigator Brunch during GKTR 2025.
Hosted by TELUX, this 2-hour event brings together physicians to discuss the future of LUMINA in a waterfront setting.
Audience:
Physicians in the pain management and medical device space. The tone should be sophisticated and professional, but elevated and engaging—not clinical or bland.
Design Requirements:
Bold and modern visual style that grabs attention
Must include the TELUX logo (primary brand) and CORA FLEX BT logo (subsidiary)
Include the GKTR conference logo to indicate the event alignment
Reflect our TELUX brand colors, with bonus points for incorporating complementary elements of CORA FLEX BT’s color palette
Layout should highlight that this is a “Save the Date” for a LUMINA Study investigator brunch aboard a yacht
Design should feel exclusive and premium, but still professional
We will provide all logos and branding guidelines. The final design will be used in both digital and printed formats. Looking for a clean layout with strong typography and sleek design elements.
Target Market(s)
Physicians
Industry/Entity Type
Medical Device

```html
<!DOCTYPE html>
<html lang="en">
<head>
<meta charset="utf-8">
<title>Save the Date – LUMINA Study Network Forum</title>
<link href="https://fonts.googleapis.com/css2?family=Cinzel:wght@400;600&family=Cinzel+Decorative:wght@400&family=Cormorant+Garamond:wght@400;500&display=swap" rel="stylesheet">
<style>
  :root{
    --night:#0b0905;
    --gold:#e2b64c;
    --gold-light:#f7dc8a;
    --gold-deep:#a9791f;
    --cream:#f3ead6;
    --sea:#3f8fae;
    --sky:#9fd0e8;
  }
  *{margin:0;padding:0;box-sizing:border-box}
  html,body{width:696px;height:1200px;overflow:hidden;background:var(--night)}
  .invite{position:relative;width:696px;height:1200px;overflow:hidden;
    background:radial-gradient(ellipse at 50% 100%,#1c150a 0%,var(--night) 70%);
    color:var(--cream);font-family:"Cormorant Garamond",serif}
  .scene{position:absolute;left:0;top:0;width:696px;height:820px;
    background:
      radial-gradient(ellipse 36% 34% at 50% 37%,var(--sky) 0%,var(--sea) 55%,rgba(63,143,174,0) 100%),
      radial-gradient(ellipse at 50% 60%,#e9c45e 0%,#b9862a 55%,#5a3c10 100%);
    -webkit-mask-image:linear-gradient(to bottom,#000 78%,transparent 100%);
            mask-image:linear-gradient(to bottom,#000 78%,transparent 100%)}
  .brand-bar{position:absolute;top:38px;left:0;width:100%;display:flex;
    justify-content:center;align-items:center;gap:22px;
    font-family:"Cinzel",serif;font-weight:600;color:#fff;letter-spacing:1px}
  .brand-bar .host{font-size:26px}
  .brand-bar .conference{display:flex;align-items:center;gap:6px;font-size:14px}
  .brand-bar .conference i{display:block;width:14px;height:14px;border-radius:50%;background:#fff}
  .headline{position:absolute;top:722px;width:100%;text-align:center;
    font-family:"Cinzel Decorative",serif;font-size:63px;line-height:1;
    color:var(--gold);letter-spacing:1px}
  .event-name{position:absolute;top:802px;width:100%;text-align:center;
    font-family:"Cinzel",serif;font-weight:600;font-size:30px;line-height:1;
    color:var(--gold);letter-spacing:1px}
  .date-row{position:absolute;top:858px;left:0;width:100%;height:80px}
  .date-row .rule{position:absolute;height:1px;
    background:linear-gradient(90deg,transparent,var(--gold) 30%,var(--gold-light) 60%,transparent)}
  .date-row .side{position:absolute;top:28px;font-size:27px;color:var(--cream);text-align:center}
  .date-row .day{position:absolute;left:298px;width:100px;top:0;text-align:center;
    font-size:44px;line-height:44px;color:#fff}
  .venue{position:absolute;top:958px;width:100%;text-align:center;
    font-family:"Cinzel Decorative",serif;font-size:40px;color:var(--gold)}
  .venue-note{position:absolute;top:1007px;width:100%;text-align:center;font-size:16px;color:var(--cream)}
  .blurb{position:absolute;top:1046px;left:90px;width:516px;text-align:center;
    font-size:20px;line-height:22px;color:var(--cream)}
</style>
</head>
<body>
<main class="invite">
  <div class="scene" role="img" aria-label="Golden-lit yacht dining room with a set round table before a porthole window overlooking sailboats on a blue sea"></div>

  <header class="brand-bar">
    <span class="host">CORA FLEX BT</span>
    <span class="conference"><i></i>GKTR 2025</span>
    <span class="host">TELUX</span>
  </header>

  <h1 class="headline">SAVE THE DATE</h1>
  <h2 class="event-name">LUMINA Study Network Forum</h2>

  <section class="date-row">
    <div class="rule" style="left:85px;width:201px;top:18px"></div>
    <div class="rule" style="left:85px;width:201px;top:64px"></div>
    <div class="rule" style="left:411px;width:201px;top:18px"></div>
    <div class="rule" style="left:411px;width:201px;top:64px"></div>
    <div class="side" style="left:85px;width:201px">9:30am - 11:30am</div>
    <div class="day">19th<br>SAT</div>
    <div class="side" style="left:411px;width:201px">July 2025</div>
  </section>

  <p class="venue">Marlo Belle Yacht</p>
  <p class="venue-note">(docked directly outside of the Westerhaven)</p>
  <p class="blurb">Join us aboard Marlo Belle for a LUMINA Study Investigator Brunch during GKTR 2025. Hosted by TELUX, this 2-hour event brings together physicians to discuss the future of LUMINA in a waterfront setting.</p>
</main>
</body>
</html>
```